Flyer-Design für Hochzeitswebseiten
Zielgruppe
Wir machen Hochzeitswebseiten ( www.holdyourglimmer.de).
Aufgabenstellung
Gerne hätte ich folgendes DIN Format: 210x148 quer mit 6 Seiten. 1 Seite schwarz mit unserem Logo. 2 Seite Bild. 3 Seite Text. 4 Seite 4-5 Bilder. 5 Seite Text. 6 Seite Kontaktinformationen.
Text1:
Ihr habt alles dafür getan, dass Eure Hochzeit so schön wie möglich wird. Wir tun alles dafür, dass die Erinnerung daran so großartig wie möglich bleibt. Ihr stellt uns Eure persönlichen Informationen und Fotos zur Verfügung. Wir machen daraus eine professionelle Website über den schönsten Tag Eures Lebens. Ihr entscheidet über Umfang und Budget.
Wir widmen uns jedem Auftrag mit Begeisterung und Kreativität.
Text2: evtl. sollte da das Basic und Premiumpaket beschrieben werden. Sind uns da aber unsicher.

```html
<!DOCTYPE html>
<html lang="de">
<head>
<meta charset="utf-8">
<title>Glimmerwerk – Flyer</title>
<link href="https://fonts.googleapis.com/css2?family=Great+Vibes&family=Noto+Serif:wght@400;700&display=swap" rel="stylesheet">
<style>
:root{
  --stage:#7a9092;
  --sheet:#ffffff;
  --rose:#e8bdc5;
  --gold:#c9961e;
  --gold-light:#e6c15a;
  --ink:#5a4a4d;
  --grey:#6d6d6d;
  --black:#000000;
}
*{margin:0;padding:0;box-sizing:border-box}
html,body{width:1200px;height:646px;overflow:hidden;background:var(--stage)}
body{position:relative;font-family:"Noto Serif",serif;color:var(--ink)}
.strip{position:absolute;left:23px;width:1164px;height:273px;background:var(--sheet);box-shadow:4px 6px 8px rgba(0,0,0,.35)}
.strip--top{top:32px}
.strip--bottom{top:326px}
.panel{position:absolute;overflow:hidden}
.strip .panel{top:10px;width:370px;height:254px}
.panel--1{left:10px}
.panel--2{left:397px}
.panel--3{left:785px}
.rose{background:var(--rose)}
.framed{border:2px solid var(--gold-light);outline:1px solid var(--gold);outline-offset:-3px}

/* pricing */
.card{position:absolute;top:8px;height:238px;background:#fff;font-size:6.6px;line-height:11px}
.card--basic{left:7px;width:134px;border:1.5px solid #a9a9a9;padding:8px 7px}
.card--premium{left:146px;width:216px;border:1.5px solid var(--gold);padding:8px 7px}
.card h2{font-family:"Great Vibes",cursive;font-weight:400;font-size:24px;line-height:26px;margin:0 0 2px 7px}
.card--basic h2{color:var(--grey)}
.card--premium h2{color:var(--gold)}
.price{font-size:6px;font-weight:700;color:var(--ink);white-space:nowrap}
.price small{font-weight:400;font-size:4.6px}
.lead{font-size:8px;line-height:13px;margin:2px 0 5px;white-space:nowrap}
.card--basic .lead{color:var(--grey)}
.card--premium .lead{color:var(--gold)}
.features{list-style:none}
.features li{padding-left:5px;position:relative;white-space:nowrap}
.features li::before{content:"";position:absolute;left:0;top:4.5px;width:2.6px;height:2.6px;border-radius:50%}
.card--basic .features li::before{background:#8d8d8d}
.card--premium .features li::before{background:var(--gold)}
.features li.indent{padding-left:10px}
.features li.indent::before{display:none}
.features li.flush{padding-left:0}
.features li.gap{margin-top:4px}
.col{position:absolute}
.col--a{left:7px;top:36px;width:102px}
.col--b{left:110px;top:40px;width:100px}
.optional{color:var(--gold);font-size:8px;line-height:11px;margin:8px 0 9px}

/* contact */
.wordmark{position:absolute;left:0;right:0;text-align:center;font-weight:400;letter-spacing:2px}
.panel--contact .wordmark{top:84px;font-size:26px;color:var(--gold)}
.contact{position:absolute;left:130px;top:141px;list-style:none;font-size:7.6px;color:var(--ink)}
.contact li{display:flex;align-items:center;height:30px}
.contact svg{width:26px;height:26px;margin-right:3px}

/* cover */
.panel--cover{background:var(--black)}
.panel--cover .wordmark{top:104px;font-size:32px;color:var(--gold-light)}

/* text page */
.story{position:absolute;left:0;right:0;top:16px;text-align:center;font-size:8.7px;line-height:11.6px;color:#fff}
.story p{margin-bottom:6px}
.story .dark{color:var(--ink)}
.story em{font-family:"Great Vibes",cursive;font-style:normal;color:var(--gold);font-size:21px;line-height:11px;margin-right:3px}

/* photo fills */
.photo{position:absolute}
.photo--kiss{inset:0;background:linear-gradient(135deg,#b7c6d6 0%,#5b7fa6 35%,#c79a86 60%,#efe5dc 100%)}
.panel--gallery{background:#fff}
.photo--beach{left:0;top:0;width:226px;height:109px;background:linear-gradient(180deg,#d9cdbf 0%,#f2d3a5 45%,#d8b9a0 100%)}
.photo--flowers{left:0;top:116px;width:86px;height:136px;background:linear-gradient(160deg,#8fb1cf,#e9e3e4 50%,#4d6a3e)}
.photo--bridesmaids{left:94px;top:116px;width:132px;height:66px;background:linear-gradient(135deg,#f1f0ee,#cfc6d6 50%,#f7f5f3)}
.photo--table{left:94px;top:190px;width:132px;height:63px;background:linear-gradient(160deg,#f4f2f4,#bfa8c8 60%,#6f4b7d)}
.photo--couple{left:235px;top:0;width:135px;height:253px;background:linear-gradient(135deg,#e9e4db,#c9ab8f 45%,#3a302c 100%)}
</style>
</head>
<body>

<section class="strip strip--top">
  <div class="panel panel--1 rose">
    <article class="card card--basic">
      <h2>Basic</h2>
      <p class="price">299.– Euro (einmalig) <small>inkl. MwSt</small></p>
      <p class="lead">Unser Grundpaket mit</p>
      <ul class="features">
        <li>50GB Speicherplatz</li>
        <li>50 Fotos</li>
        <li>Eine Wunschdomain</li>
        <li>Eigene E-Mailadresse</li>
        <li>Passwortschutz</li>
        <li>SSL Zertifikat</li>
        <li>Keine Werbung</li>
        <li>Optimiert für Smartphones und</li>
        <li class="indent">Tablets</li>
        <li>Keine Verpflichtungen</li>
        <li>Keine automatische Verlängerung</li>
        <li>Eure Webseite als ZIP-Datei</li>
        <li>Hosting &amp; Serverkosten für 1 Jahr</li>
        <li class="gap">Auf Wunsch: Save the Date</li>
      </ul>
    </article>
    <article class="card card--premium">
      <h2>Premium</h2>
      <div class="col col--a">
        <p class="price">429.– Euro (einmalig) <small>inkl. MwSt</small></p>
        <p class="lead">Unser Premiumpaket mit</p>
        <ul class="features">
          <li>Unbegrenzter Speicherplatz</li>
          <li>Unbegrenzte Anzahl an Fotos</li>
          <li>Euer Hochzeitsvideo</li>
          <li>Eine Wunschdomain</li>
          <li>Eigene E-Mailadresse</li>
          <li>Ausführliche Berichte</li>
          <li>Gästebuch</li>
          <li>Verknüpfung Social Media &amp;</li>
          <li class="indent">Fotoportale</li>
          <li>Passwortschutz</li>
          <li>SSL-Zertifikat</li>
          <li>Keine Werbung</li>
          <li>Optimiert für Smartphones</li>
          <li class="flush">und Tablets</li>
        </ul>
      </div>
      <div class="col col--b">
        <ul class="features">
          <li>Keine Verpflichtungen</li>
          <li>Keine automatische</li>
          <li class="indent">Verlängerung</li>
          <li>Eure Webseite als ZIP-Datei</li>
          <li>Hosting &amp; Serverkosten für</li>
          <li class="indent">ein Jahr</li>
          <li class="gap">Auf Wunsch: Save the Date</li>
        </ul>
        <p class="optional">Optional könnt Ihr Eure<br>Webseite erweitern mit:</p>
        <ul class="features">
          <li>Eure Flitterwochen</li>
          <li>Euren Hochzeitstag</li>
          <li>Geburt Eurer Kinder</li>
          <li>Eure Urlaube</li>
          <li>Jubilar</li>
          <li>...etc...</li>
        </ul>
      </div>
    </article>
  </div>

  <div class="panel panel--2 panel--contact rose framed">
    <p class="wordmark">GLIMMERWERK</p>
    <ul class="contact">
      <li>
        <svg viewBox="0 0 26 26" aria-hidden="true"><path d="M13 1a12 12 0 1 1-8 21" fill="none" stroke="#c9961e" stroke-width="1.4"/><path d="M9 7l3-1 2 4-2 1.5c.8 2 2 3.3 3.8 4.2L17.5 14l3.5 2.2-1 3C13 19 8.5 13 9 7z" fill="#d9a832"/></svg>
        +49 (0) 221 55 01 27 86
      </li>
      <li>
        <svg viewBox="0 0 26 26" aria-hidden="true"><path d="M13 1a12 12 0 1 1-8 21" fill="none" stroke="#c9961e" stroke-width="1.4"/><rect x="5" y="8" width="16" height="10" fill="#e6c15a"/><path d="M5 8l8 6 8-6" fill="none" stroke="#b8860b" stroke-width="1"/></svg>
        info@holdyourglimmer.de
      </li>
      <li>
        <svg viewBox="0 0 26 26" aria-hidden="true"><path d="M13 1a12 12 0 1 1-8 21" fill="none" stroke="#c9961e" stroke-width="1.4"/><circle cx="13" cy="13" r="7" fill="#e6c15a"/><path d="M6 13h14M13 6v14M8 9h10M8 17h10" stroke="#b8860b" stroke-width=".8"/></svg>
        www.holdyourglimmer.de
      </li>
    </ul>
  </div>

  <div class="panel panel--3 panel--cover">
    <p class="wordmark">GLIMMERWERK</p>
  </div>
</section>

<section class="strip strip--bottom">
  <div class="panel panel--1">
    <div class="photo photo--kiss" role="img" aria-label="Foto: Brautpaar küsst sich, Braut mit Blumenkranz im Haar"></div>
  </div>

  <div class="panel panel--2 rose framed">
    <div class="story">
      <p><em>Ihr</em><span class="dark">habt alles dafür getan,<br>dass Eure Hochzeit<br>so schön wie möglich wird.</span><br><em>Wir</em>tun alles dafür, dass die Erinnerung<br>daran so großartig<br>wie möglich bleibt.</p>
      <p style="margin-top:14px"><em>Ihr</em><span class="dark">stellt uns Eure<br>persönlichen Informationen<br>und Fotos zur Verfügung.</span><br><em>Wir</em>machen daraus eine professionelle<br>Website über den schönsten Tag Eures Lebens.</p>
      <p style="margin-top:14px"><em>Ihr</em><span class="dark">entscheidet über<br>Umfang und Budget.</span><br><em>Wir</em>widmen uns jedem Auftrag mit<br>Begeisterung und Kreativität.</p>
    </div>
  </div>

  <div class="panel panel--3 panel--gallery">
    <div class="photo photo--beach" role="img" aria-label="Foto: Brautpaar Hand in Hand am Strand bei Sonnenuntergang"></div>
    <div class="photo photo--flowers" role="img" aria-label="Foto: Blumenstrauß in einer Glasvase"></div>
    <div class="photo photo--bridesmaids" role="img" aria-label="Foto: Braut mit Brautjungfern und Sträußen"></div>
    <div class="photo photo--table" role="img" aria-label="Foto: gedeckte Hochzeitstafel in Weiß und Violett"></div>
    <div class="photo photo--couple" role="img" aria-label="Foto: Brautpaar Stirn an Stirn"></div>
  </div>
</section>

</body>
</html>
```